Healthcare and Professional IT Services Company need a redesigned business card

We are a IT Services company that targets small medical practices and professional business such as Attorneys, Accounts, Architects etc. We want to communicate a professional yet friendly image using recent logo redesign here on ArtHarbor. Like to see the colors blue and orange in the design. Must use the Tall Pine Computing as displayed in the new logo - then also want to incorporate the fish logo as well.

Target Market(s)

Small medical and professional services

Industry/Entity Type

It Company

Contact Information for Business Card

The usual stuff, place for name address phone website. Also maybe our tagline which is "rooted in technology"

Requirements
Must have
• My new logo and the fish somewhere on the card

```html
<!DOCTYPE html>
<html lang="en">
<head>
<meta charset="utf-8">
<title>Tall Pine Computing – Business Card</title>
<link rel="stylesheet" href="https://fonts.googleapis.com/css2?family=Source+Sans+3:ital,wght@0,400;0,600;1,700&display=swap">
<style>
  :root {
    --stage: #000000;
    --card: #333437;
    --card-edge: #3a3b3f;
    --blue: #2aa3dc;
    --orange: #f07c3c;
    --text: #ffffff;
    --rule: #4a4b50;
  }
  * { box-sizing: border-box; margin: 0; padding: 0; }
  html, body {
    width: 1200px; height: 900px; overflow: hidden;
    background: var(--stage);
    font-family: "Source Sans 3", "Myriad Pro", Arial, sans-serif;
  }
  .canvas { position: relative; width: 1200px; height: 900px; }
  .card {
    position: absolute; top: 271px;
    width: 457px; height: 281px;
    background: var(--card);
    border-radius: 14px;
    box-shadow: inset 0 0 0 1px var(--card-edge);
  }
  .card--front { left: 137px; }
  .card--back  { left: 626px; }

  .mascot-art {
    position: absolute; left: 36px; top: 80px;
    width: 172px; height: 120px;
    border-radius: 46% 54% 50% 50% / 55% 55% 45% 45%;
    background: radial-gradient(ellipse at 60% 45%, #4cc4cf 0%, #2b8fc9 55%, #e6784a 100%);
  }
  .divider {
    position: absolute; left: 228px; top: 80px;
    width: 1px; height: 120px; background: var(--rule);
  }
  .details { position: absolute; left: 249px; top: 63px; color: var(--text); }
  .details__name { font-size: 19px; font-weight: 400; color: var(--blue); line-height: 24px; }
  .details__role { font-size: 13px; line-height: 17px; margin-bottom: 9px; }
  .details__address { font-size: 13px; line-height: 16.5px; margin-bottom: 8px; font-style: normal; }
  .contact-list { list-style: none; font-size: 13px; line-height: 16.5px; }
  .contact-list li { display: flex; align-items: center; gap: 6px; }
  .contact-list svg { width: 10px; height: 10px; flex: none; }

  .brand {
    position: absolute; left: 0; right: 0; top: 160px;
    text-align: center;
    font-size: 28px; font-weight: 600; color: var(--blue);
    line-height: 32px;
  }
  .brand__mark {
    position: absolute; left: 50%; top: 76px;
    width: 54px; height: 54px; margin-left: -27px;
    border-radius: 50%; background: var(--orange);
  }
  .tagline {
    position: absolute; left: 0; right: 0; top: 217px;
    text-align: center;
    font-size: 14.5px; font-weight: 700; font-style: italic; color: var(--blue);
  }
</style>
</head>
<body>
<main class="canvas">
  <section class="card card--front">
    <div class="mascot-art" role="img" aria-label="Cartoon fish mascot illustration in blue and orange"></div>
    <div class="divider"></div>
    <div class="details">
      <p class="details__name">Daniel Morgan</p>
      <p class="details__role">Managing Director</p>
      <address class="details__address">12345, Address Goes Here<br>Country Name, 123456.</address>
      <ul class="contact-list">
        <li>
          <svg viewBox="0 0 10 10" aria-hidden="true"><path fill="#2aa3dc" d="M2 0.5 L3.6 2.6 L2.8 3.6 Q4 6 6.4 7.2 L7.4 6.4 L9.5 8 L8.4 9.5 Q4.5 9.5 1.8 6.6 Q0.3 4.5 0.5 1.6 Z"/></svg>
          <span>044-123 456 789</span>
        </li>
        <li>
          <svg viewBox="0 0 10 10" aria-hidden="true"><rect x="0.5" y="2" width="9" height="6.5" fill="#2aa3dc"/><path d="M0.8 2.3 L5 5.5 L9.2 2.3" fill="none" stroke="#333437" stroke-width="0.9"/></svg>
          <span>info@webname.com</span>
        </li>
        <li>
          <svg viewBox="0 0 10 10" aria-hidden="true"><g fill="none" stroke="#2aa3dc" stroke-width="1.3" stroke-linecap="round"><path d="M4.2 6.6 L2.8 8 Q1.5 9.2 0.9 8.4 Q0.4 7.6 1.8 6.2 L3.4 4.6"/><path d="M5.8 3.4 L7.2 2 Q8.5 0.8 9.1 1.6 Q9.6 2.4 8.2 3.8 L6.6 5.4"/><path d="M3.6 6.4 L6.4 3.6"/></g></svg>
          <span>www.websitename.com</span>
        </li>
      </ul>
    </div>
  </section>

  <section class="card card--back">
    <div class="brand__mark" aria-hidden="true"></div>
    <p class="brand">Tall Pine Computing</p>
    <p class="tagline">"rooted in technology"</p>
  </section>
</main>
</body>
</html>
```